I have a website called Okenta Holdings (okentaholdings.com) that I would like to have redesigned. Most of the content is already created, but I need a new design. You can also see my other website at brambleacres.com. I am open to a new logo or modifying the current logo if you have a good idea. Please feel free to use other images for the home page (and maybe some other locations) if you feel they provide a better look and feel to the website. I prefer a modern look.

Important: You do not have to use the images I've provided for the home page. Feel free to find your own stock photos. You don't have to pay for them unless I select your design.

1) Please use wix.com to make your changes so that I can edit it later.
2) I will need all the graphics files to be saved so I can dowload it for later.
3) I will be adding more content to the site later.
4) This site will likely be transferred over to brambleacres.com so if you make a logo please make one for Okenta Holdings and one for Bramble Acres.
5) You can use other images that you feel would help the look and feel of the website.

```html
<!DOCTYPE html>
<html lang="en">
<head>
<meta charset="utf-8">
<title>Okenta Holdings</title>
<link href="https://fonts.googleapis.com/css2?family=Poppins:wght@600;700;800&family=Nunito+Sans:wght@400;600;700&display=swap" rel="stylesheet">
<style>
:root{
  --navy:#23446a;
  --heading:#2a4a6e;
  --sky:#5b9bd5;
  --link:#4a8fd0;
  --card:#f5f5f5;
  --light:#f7f7f7;
  --text:#2b2b2b;
  --muted:#9a9a9a;
  --white:#ffffff;
}
*{margin:0;padding:0;box-sizing:border-box}
html,body{width:1200px;height:2974px;overflow:hidden;background:var(--white)}
body{font-family:"Nunito Sans",sans-serif;color:var(--text);position:relative}
.abs{position:absolute}
h1,h2,h3,.stat-value{font-family:"Poppins",sans-serif}
.section-title{position:absolute;left:0;width:1200px;text-align:center;font-size:22px;font-weight:700;color:var(--heading);letter-spacing:.3px}
.rule{position:absolute;left:584px;width:33px;height:3px;background:var(--heading)}

/* header */
.site-header{top:0;left:0;width:1200px;height:80px;background:var(--white)}
.brand{left:133px;top:22px;display:flex;align-items:center;gap:10px;font-family:"Nunito Sans",sans-serif;font-weight:700;font-size:25px;color:var(--link)}
.brand-mark{width:34px;height:34px;border-radius:50%;background:var(--link)}
.nav{right:134px;top:33px;display:flex;gap:41px;font-size:14.5px;font-weight:700;letter-spacing:.4px}
.nav a{color:var(--text);text-decoration:none}
.nav a.active{color:var(--link)}

/* hero */
.hero{top:80px;left:0;width:1200px;height:528px;
  background:linear-gradient(180deg,#b7a9d6 0%,#d8a8c8 22%,#f4b87a 42%,#e99a55 55%,#6e6a7a 72%,#4a4f58 100%)}
.hero-title{top:110px;left:0;width:1200px;text-align:center;font-size:33px;line-height:39px;font-weight:700;color:var(--heading)}
.hero-sub{top:202px;left:0;width:1200px;text-align:center;font-size:17.5px;font-weight:700;color:var(--heading)}

/* strategy */
.card{position:absolute;top:724px;width:224px;height:270px;background:var(--card)}
.card svg{position:absolute;left:50%;top:30px;transform:translateX(-50%)}
.card h3{position:absolute;top:116px;left:0;width:100%;text-align:center;font-size:13.5px;font-weight:700;color:var(--heading)}
.card ul{position:absolute;top:151px;list-style:none;font-size:11px;line-height:13px}
.card li{position:relative;padding-left:14px;margin-bottom:9.5px}
.card li::before{content:"";position:absolute;left:0;top:3px;border-left:5px solid var(--text);border-top:3.5px solid transparent;border-bottom:3.5px solid transparent}

/* about */
.about{top:1044px;left:0;width:570px;height:457px;background:var(--navy)}
.about-photo{top:1044px;left:570px;width:630px;height:457px;
  background:linear-gradient(110deg,#2b3440 0%,#59626e 30%,#3e6aa8 50%,#7d8a5a 72%,#3c4a2a 100%)}
.about h2{position:absolute;left:131px;top:64px;font-size:21px;font-weight:800;color:var(--white)}
.about .bar{position:absolute;left:131px;top:106px;width:76px;height:3px;background:var(--white)}
.about p{position:absolute;left:131px;top:144px;width:378px;font-size:14.5px;line-height:20.8px;color:var(--white)}

/* stats */
.stats{top:1501px;left:0;width:1200px;height:126px;background:var(--sky)}
.stat{position:absolute;top:30px;width:260px;text-align:center;color:var(--white)}
.stat-value{font-size:28px;font-weight:800;line-height:34px}
.stat-label{font-size:13px;margin-top:4px}

/* projects */
.project{position:absolute;top:1752px;width:299px;height:348px;border:1px solid #cfcfcf;background:var(--white)}
.project .photo{height:192px}
.project h3{position:absolute;left:27px;top:215px;font-size:13.5px;font-weight:700;color:var(--heading)}
.project .spec{position:absolute;left:27px;top:244px;width:200px;font-size:12px;line-height:17.5px}
.project .kind{position:absolute;left:27px;top:297px;font-size:12px}

/* partners */
.partners{top:2154px;left:0;width:1200px;height:247px;background:var(--light)}
.partner{position:absolute;top:153px;font-family:"Nunito Sans",sans-serif;font-size:26px;font-weight:600;color:var(--muted);letter-spacing:.5px}

/* contact */
.contact{top:2401px;left:0;width:1200px;height:494px;background:var(--navy)}
.contact .section-title{color:var(--white);top:40px}
.contact .rule{background:var(--white);top:83px}
.field{position:absolute;left:365px;width:470px;background:var(--white);font-size:12px;color:var(--heading);padding:14px 17px}
.submit{position:absolute;left:365px;top:403px;width:470px;height:42px;background:var(--sky);color:var(--white);font-family:"Poppins",sans-serif;font-weight:700;font-size:17px;text-align:center;line-height:42px}

/* footer */
.site-footer{top:2895px;left:0;width:1200px;height:79px}
.copyright{position:absolute;left:133px;top:36px;font-size:12.5px}
.social{position:absolute;top:33px;width:22px;height:22px;border-radius:50%;background:#111}
</style>
</head>
<body>

<header class="site-header abs">
  <div class="brand abs"><span class="brand-mark"></span>Okenta Holdings</div>
  <nav class="nav abs">
    <a class="active" href="#">HOME</a><a href="#">ABOUT</a><a href="#">STRATEGY</a><a href="#">PROJECTS</a><a href="#">CONTACT</a>
  </nav>
</header>

<div class="hero abs" role="img" aria-label="City skyline with bay bridge at sunset under a pink and purple sky"></div>
<h1 class="hero-title abs">Private Commercial Real Estate<br>Investment and Development Firm</h1>
<div class="hero-sub abs">Building together. Growing Together.</div>

<h2 class="section-title" style="top:644px">STRATEGY</h2>
<div class="rule" style="top:684px"></div>

<div class="card" style="left:133px">
  <svg width="64" height="50" viewBox="0 0 64 50" fill="none" stroke="#23446a" stroke-width="2"><circle cx="10" cy="38" r="8" fill="#23446a"/><rect x="22" y="32" width="6" height="14"/><rect x="32" y="26" width="6" height="20"/><rect x="42" y="20" width="6" height="26"/><path d="M8 26 L24 14 L34 20 L56 4 M48 4 H56 V12"/><path d="M4 46 H62"/></svg>
  <h3>Investment Focus</h3>
  <ul style="left:32px"><li>Ground-up Development</li><li>Value-Add Acquisition</li><li>Equity Financing</li><li>Debt Financing</li></ul>
</div>
<div class="card" style="left:371px">
  <svg width="54" height="52" viewBox="0 0 54 52" fill="none" stroke="#23446a" stroke-width="2"><rect x="4" y="30" width="8" height="18"/><rect x="16" y="22" width="8" height="26"/><rect x="28" y="12" width="8" height="36"/><path d="M44 48 V4 M38 10 L44 4 L50 10 M40 30 H48 M40 36 H48 M40 42 H48"/></svg>
  <h3>Development</h3>
  <ul style="left:31px"><li>Undeveloped Land</li><li>Entitled Land</li><li>Urban Redevelopment</li><li>Single Story Garden</li></ul>
</div>
<div class="card" style="left:609px">
  <svg width="60" height="60" viewBox="0 0 60 60" fill="none" stroke="#23446a" stroke-width="2"><circle cx="30" cy="30" r="27" stroke-dasharray="4 3"/><path d="M12 30 L22 22 L30 26 L38 22 L48 30 L38 38 L30 34 L22 38 Z" fill="#23446a"/></svg>
  <h3>Distressed/Value-Add</h3>
  <ul style="left:20px"><li>Major Metropolitan Areas</li><li style="margin-bottom:6px">Asset Value between<br>$10 - $75mm</li><li style="margin-bottom:6px">&nbsp;</li><li>Assets which yeild cash-on-cash<br>returns as well as rent growth<br>and exit upside.</li></ul>
</div>
<div class="card" style="left:845px">
  <svg width="60" height="60" viewBox="0 0 60 60" fill="none" stroke="#23446a" stroke-width="2"><rect x="16" y="8" width="30" height="48"/><path d="M22 2 H40 V8 M16 20 H46 M16 30 H46 M16 40 H46 M26 8 V56 M36 8 V56 M46 40 H56 V56 H2"/><ellipse cx="8" cy="44" rx="4" ry="7"/></svg>
  <h3>Product Types</h3>
  <ul style="left:28px"><li>Multifamily</li><li>Industrial</li><li>SFR Communities</li><li>Self-Storage</li></ul>
</div>

<section class="about abs">
  <h2>ABOUT US</h2>
  <div class="bar"></div>
  <p>Bramble Acres is a private real estate firm that specializes in the procurement, development, management, and disposition of various commercial real estate asset types including multifamily, industrial, single-family, hospitality, self-storage, and flex. The firm effectuates its strategy by utilizing long-standing relationships to ascertain acquisition and development opportunities within a specific target market.&nbsp; Bramble Acres is currently focused on acquisition and development opportunities in the southern portion of the United States.</p>
</section>
<div class="about-photo abs" role="img" aria-label="Modern glass residence at dusk with a lit garden walkway and reflecting pool"></div>

<section class="stats abs">
  <div class="stat" style="left:75px"><div class="stat-value">2017</div><div class="stat-label">Year Established</div></div>
  <div class="stat" style="left:331px"><div class="stat-value">Dallas, TX</div><div class="stat-label">Headquarters</div></div>
  <div class="stat" style="left:631px"><div class="stat-value">$100MM+</div><div class="stat-label">Assets Under Management</div></div>
  <div class="stat" style="left:887px"><div class="stat-value">6</div><div class="stat-label">Current Projects</div></div>
</section>

<h2 class="section-title" style="top:1667px">PROJECTS</h2>
<div class="rule" style="top:1711px"></div>

<div class="project" style="left:133px">
  <div class="photo" role="img" aria-label="Rendering of a four-story apartment building with trees and a street" style="background:linear-gradient(180deg,#b9cbe0 0%,#d9d2c2 45%,#8a8a6a 75%,#5f7a45 100%)"></div>
  <h3>Larkspur Landing Residences</h3>
  <div class="spec">Class A Multifamily - 176 Units - 4 Story - 159,280 SF - 3 Acres</div>
  <div class="kind">Ground-up Development</div>
</div>
<div class="project" style="left:450px">
  <div class="photo" role="img" aria-label="Rendering of a multifamily complex with a courtyard pool" style="background:linear-gradient(180deg,#e8ecf0 0%,#6b5a50 40%,#4a4a4a 62%,#8fae70 100%)"></div>
  <h3>Willowmere at Cedar Bend</h3>
  <div class="spec">Class A Multifamily - 373 Units - 3 Story - 345,297 SF - 24.31 Acres</div>
  <div class="kind">Ground-up Development</div>
</div>
<div class="project" style="left:769px">
  <div class="photo" role="img" aria-label="White industrial warehouse building under a blue sky" style="background:linear-gradient(180deg,#2e6fd0 0%,#7fa9e0 30%,#e8eaec 50%,#c9cbce 80%,#8c8f93 100%)"></div>
  <h3>Dallas Industrial</h3>
  <div class="spec" style="width:230px">Class A Industrial - 170,000 SF - 10.10 Acres</div>
  <div class="kind">Ground-up Development</div>
</div>

<section class="partners abs">
  <h2 class="section-title" style="top:43px">CORPORATE PARTNERS</h2>
  <div class="rule" style="top:87px"></div>
  <div class="partner" style="left:188px">NORVALE</div>
  <div class="partner" style="left:350px">BRISTEN</div>
  <div class="partner" style="left:516px">Calmora</div>
  <div class="partner" style="left:668px">HALDEN</div>
  <div class="partner" style="left:832px">FENWICK</div>
</section>

<section class="contact abs">
  <h2 class="section-title">CONTACT US</h2>
  <div class="rule"></div>
  <div class="field" style="top:121px;height:42px">Full Name</div>
  <div class="field" style="top:176px;height:43px">Email</div>
  <div class="field" style="top:229px;height:42px">Phone</div>
  <div class="field" style="top:280px;height:107px">Message</div>
  <div class="submit">SUBMIT</div>
</section>

<footer class="site-footer abs">
  <div class="copyright">Copyright © 2022 All Rights Reserved</div>
  <span class="social" style="left:1012px" aria-label="Social profile"></span>
  <span class="social" style="left:1044px" aria-label="Social profile"></span>
</footer>

</body>
</html>
```